Fun relaxed Travel Photography Business Card*

Require a fun, funky and quirky but rememberable business card for a travel photographer

Industry/Entity Type

Photographer

Contact Information for Business Card

Front Card

(my name) Lenn D.

Travel Photographer ( small under travel photographer) “self-proclaimed”

(website logo) wanderingsoflenn.net

(Instagram logo) @wanderings_of_lenn

(Instagram logo) @wanderings_of_lenn_2.0 (backup for when Instagram puts Lenn on timeout for bad behaviour)

Tel: N/A (removing the potential awkwardness of me not replying)

Email: (see above)

Back Card

Offending people since 1986

(Bottom right corner) “p.s. travelling made me fatTER”

Font styles to use
Serif

Colors

Designer to choose colors to be used in the design.

Requirements
Must have
• a camera
• a similar cartoon version of me as the "logo" see attached files, try to make as similar as possible

```html
<!DOCTYPE html>
<html lang="en">
<head>
<meta charset="utf-8">
<title>Lenn D. – Travel Photographer Business Cards</title>
<link rel="stylesheet" href="https://fonts.googleapis.com/css2?family=Open+Sans:wght@400;600&display=swap">
<style>
  :root {
    --stage: #1c1e20;
    --stage-light: #2a2d30;
    --card-blue: #2b546f;
    --accent-yellow: #f1bf3b;
    --text-white: #f4f4f2;
    --text-dark: #2b3a44;
    --figure-brown: #6b3f22;
  }
  * { margin: 0; padding: 0; box-sizing: border-box; }
  html, body {
    width: 1200px;
    height: 1200px;
    overflow: hidden;
  }
  body {
    background: radial-gradient(circle at 50% 35%, var(--stage-light), var(--stage) 75%);
    font-family: "Open Sans", Arial, sans-serif;
    display: flex;
    flex-direction: column;
    align-items: center;
    justify-content: center;
    gap: 80px;
  }
  .card {
    position: relative;
    width: 700px;
    height: 400px;
    background: var(--card-blue);
    border-radius: 8px;
    overflow: hidden;
    box-shadow: 0 20px 40px rgba(0,0,0,0.5);
  }

  /* Front */
  .mascot {
    position: absolute;
    left: 110px;
    top: 95px;
    width: 210px;
    height: 230px;
    border-radius: 12px;
    background: linear-gradient(160deg, var(--accent-yellow) 0%, #e0a62c 55%, var(--figure-brown) 100%);
  }
  .divider {
    position: absolute;
    left: 352px;
    top: 90px;
    height: 220px;
    border-left: 2px dashed var(--accent-yellow);
  }
  .identity {
    position: absolute;
    left: 378px;
    top: 92px;
    color: var(--text-white);
  }
  .identity .name {
    color: var(--accent-yellow);
    font-size: 30px;
    font-weight: 400;
    letter-spacing: 2px;
    line-height: 1.1;
    text-transform: uppercase;
  }
  .identity .role {
    font-size: 19px;
    letter-spacing: 0.5px;
    line-height: 1.2;
  }
  .identity .role-note {
    font-size: 14px;
    line-height: 1.2;
  }
  .contacts {
    position: absolute;
    left: 378px;
    top: 208px;
    list-style: none;
    color: var(--text-white);
    font-size: 14px;
  }
  .contacts li {
    display: flex;
    align-items: center;
    gap: 10px;
    margin-bottom: 14px;
  }
  .contacts svg { flex: none; }

  /* Back */
  .slogan {
    position: absolute;
    left: 0;
    right: 0;
    top: 0;
    height: 312px;
    display: flex;
    align-items: center;
    justify-content: center;
    color: var(--accent-yellow);
    font-size: 27px;
    letter-spacing: 1.5px;
  }
  .footer-band {
    position: absolute;
    left: 0;
    right: 0;
    bottom: 0;
    height: 88px;
    background: var(--accent-yellow);
  }
  .footer-band .postscript {
    position: absolute;
    right: 40px;
    top: 10px;
    color: var(--text-dark);
    font-size: 14px;
  }
</style>
</head>
<body>
  <section class="card card-front">
    <div class="mascot" role="img" aria-label="Cartoon of the photographer in sunglasses and a floral shirt lounging in a yellow beach chair beside a small table with a drink"></div>
    <div class="divider"></div>
    <div class="identity">
      <h1 class="name">Lenn D.</h1>
      <p class="role">TRAVEL PHOTOGRAPHER</p>
      <p class="role-note">self-proclaimed</p>
    </div>
    <ul class="contacts">
      <li>
        <svg width="16" height="16" viewBox="0 0 16 16" aria-hidden="true"><circle cx="8" cy="8" r="6.5" fill="none" stroke="#f1bf3b" stroke-width="1.6"/><ellipse cx="8" cy="8" rx="3" ry="6.5" fill="none" stroke="#f1bf3b" stroke-width="1.2"/><line x1="1.5" y1="8" x2="14.5" y2="8" stroke="#f1bf3b" stroke-width="1.2"/></svg>
        <span>wanderingsoflenn.net</span>
      </li>
      <li>
        <svg width="16" height="16" viewBox="0 0 16 16" aria-hidden="true"><rect x="1" y="1" width="14" height="14" rx="3" fill="#f1bf3b"/></svg>
        <span>@wanderings_of_lenn</span>
      </li>
      <li>
        <svg width="16" height="16" viewBox="0 0 16 16" aria-hidden="true"><rect x="1" y="1" width="14" height="14" rx="3" fill="#f1bf3b"/></svg>
        <span>@wanderings_of_lenn_2.0</span>
      </li>
    </ul>
  </section>

  <section class="card card-back">
    <p class="slogan">OFFENDING PEOPLE SINCE 1986</p>
    <div class="footer-band">
      <p class="postscript">p.s. travelling made me fatTER</p>
    </div>
  </section>
</body>
</html>
```